K & R Acre Works. Business card design

We need a business card designed for a new business. We have a bulldozer and tractor service. We clear land and make wildlife food plots. We provide disking, bush hogging, and site prep services.
I have attached an image of a business card that I like and would like my business cards to look similar.

Target Market(s)

anyone needing bulldozer and/or tractor services

Industry/Entity Type

Business

Contact Information for Business Card

K & R Acre Works, Operated by 7-T-Ranch
Wade Colton
601-472-3358
wcr4817@fieldmail-example.com

Font styles to use
Sans Serif

Colors

Designer to choose colors to be used in the design.

Requirements
Must have
• image of tractor and bulldozer
• Land Clearing
• Wildlife food plots
• Bush Hogging
• Disking
• Site prep
Nice to have
• i have included a image of a business card that i like. I would like mine to be similar.

```html
<!DOCTYPE html>
<html lang="en">
<head>
<meta charset="utf-8">
<title>K &amp; R Acre Works — Business Card</title>
<link href="https://fonts.googleapis.com/css2?family=Bebas+Neue&family=Oswald:wght@300;500&family=Roboto:wght@400&display=swap" rel="stylesheet">
<style>
  :root {
    --bg: #e9e6e1;
    --card: #ffffff;
    --card-shade: #eeeeee;
    --red: #e8463d;
    --ink: #222222;
    --grey: #5d5d5d;
    --grass: #6f8a3c;
    --soil: #9a8260;
    --tractor: #d9542f;
    --dozer: #d8b93a;
    --sky: #a9c6de;
  }
  * { margin: 0; padding: 0; box-sizing: border-box; }
  html, body { width: 1200px; height: 1023px; overflow: hidden; background: var(--bg); }
  .canvas { position: relative; width: 1200px; height: 1023px; }
  .card {
    position: absolute; left: 100px; top: 226px; width: 1000px; height: 571px;
    background: linear-gradient(160deg, var(--card) 40%, var(--card-shade));
    box-shadow: 0 10px 30px rgba(0,0,0,.18);
    overflow: hidden;
  }
  .brand { position: absolute; left: 60px; top: 70px; }
  .brand-name {
    font-family: "Bebas Neue", sans-serif; font-size: 64px; line-height: 1;
    color: var(--red); letter-spacing: 1px;
  }
  .brand-operator {
    font-family: "Oswald", sans-serif; font-weight: 300; font-size: 22px;
    letter-spacing: 5px; color: var(--grey); text-transform: uppercase; margin-top: 4px;
  }
  .services {
    position: absolute; left: 60px; top: 225px;
    font-family: "Oswald", sans-serif; font-weight: 500; font-size: 25px;
    line-height: 1.35; color: var(--ink); text-transform: uppercase;
  }
  .services .sep { color: var(--red); padding: 0 6px; }
  .contact { position: absolute; left: 590px; top: 60px; }
  .contact-name {
    font-family: "Bebas Neue", sans-serif; font-size: 70px; line-height: 1;
    color: var(--red); letter-spacing: 2px;
  }
  .contact-line {
    display: flex; align-items: center; gap: 14px; margin-top: 14px;
    font-family: "Roboto", sans-serif; font-size: 25px; color: var(--ink);
  }
  .contact-line svg { width: 20px; height: 20px; flex: none; }
  .contact-email { font-size: 19px; }
  .photo-strip { position: absolute; left: 0; bottom: 0; width: 1000px; height: 215px; }
</style>
</head>
<body>
<div class="canvas">
  <article class="card">
    <div class="brand">
      <div class="brand-name">K &amp; R Acre Works</div>
      <div class="brand-operator">Operated by 7-T-Ranch</div>
    </div>
    <div class="services">
      <div>Land Clearing<span class="sep">-</span>Wildlife Food Plots</div>
      <div>Bush Hogging<span class="sep">-</span>Disking<span class="sep">-</span>Site Prep</div>
    </div>
    <div class="contact">
      <div class="contact-name">Wade Colton</div>
      <div class="contact-line">
        <svg viewBox="0 0 20 20" aria-hidden="true"><path d="M5 2 L8 6 L6 8 C7 11 9 13 12 14 L14 12 L18 15 L16 18 C9 18 2 11 2 4 Z" fill="none" stroke="var(--red)" stroke-width="1.8" stroke-linejoin="round"/></svg>
        <span>601-472-3358</span>
      </div>
      <div class="contact-line contact-email">
        <svg viewBox="0 0 20 20" aria-hidden="true"><rect x="2" y="4" width="16" height="12" fill="none" stroke="var(--red)" stroke-width="1.8"/><path d="M2 4 L10 11 L18 4" fill="none" stroke="var(--red)" stroke-width="1.8"/></svg>
        <span>wcr4817@fieldmail-example.com</span>
      </div>
    </div>
    <svg class="photo-strip" viewBox="0 0 1000 215">
      <defs>
        <linearGradient id="photo-tractor" x1="0" y1="0" x2="0" y2="1">
          <stop offset="0" stop-color="#7d9a4a"/><stop offset=".6" stop-color="var(--tractor)"/><stop offset="1" stop-color="#6c6a44"/>
        </linearGradient>
        <linearGradient id="photo-dozer-dirt" x1="0" y1="0" x2="0" y2="1">
          <stop offset="0" stop-color="var(--sky)"/><stop offset=".5" stop-color="var(--dozer)"/><stop offset="1" stop-color="var(--soil)"/>
        </linearGradient>
        <linearGradient id="photo-dozer-trees" x1="0" y1="0" x2="0" y2="1">
          <stop offset="0" stop-color="#4d6a3a"/><stop offset=".55" stop-color="var(--dozer)"/><stop offset="1" stop-color="#4b4a42"/>
        </linearGradient>
        <linearGradient id="photo-dozer-field" x1="0" y1="0" x2="0" y2="1">
          <stop offset="0" stop-color="var(--grass)"/><stop offset=".5" stop-color="#c9b24a"/><stop offset="1" stop-color="#b7a481"/>
        </linearGradient>
      </defs>
      <rect x="0" y="10" width="250" height="205" fill="url(#photo-tractor)" role="img" aria-label="Photo of a red tractor with a bush hog in tall grass"/>
      <rect x="250" y="10" width="250" height="205" fill="url(#photo-dozer-dirt)" role="img" aria-label="Photo of a yellow bulldozer pushing dirt"/>
      <rect x="500" y="10" width="250" height="205" fill="url(#photo-dozer-trees)" role="img" aria-label="Photo of a yellow bulldozer clearing trees"/>
      <rect x="750" y="10" width="250" height="205" fill="url(#photo-dozer-field)" role="img" aria-label="Photo of a bulldozer on a cleared field"/>
      <rect x="0" y="0" width="1000" height="10" fill="var(--card)"/>
      <line x1="0" y1="8" x2="1000" y2="8" stroke="var(--red)" stroke-width="5"/>
    </svg>
  </article>
</div>
</body>
</html>
```